New Interrior Decoration company needs new website

We need a website for our new company specialising in interior decoration to residential and commercial markets.
We supply and install decorative and printed films for office and home decoration such as feature walls.
We would like to keep the design simple and clean.

Target Market(s)

Architects and interior designaers

Industry/Entity Type

It Company

Number of Pages Required

5+ page

Font styles to use
Sans Serif

Requirements
Must have
• Home page,
• Services/products page (split into commercial and residential)
• Gallery (split into commercial and residential)
• contact form and page
Nice to have
• Very clean and minimalistic design.

```html
<!DOCTYPE html>
<html lang="en">
<head>
<meta charset="utf-8">
<title>Vantage Interiors</title>
<link href="https://fonts.googleapis.com/css2?family=Roboto:wght@300;400;500;700&display=swap" rel="stylesheet">
<style>
:root{
  --blue:#0a5bbf;
  --blue-text:#1a5fb4;
  --white:#ffffff;
  --dark:#1c1c1d;
  --cta:#232427;
  --footer:#26272b;
  --grey-text:#8a8a8a;
  --footer-text:#a4a5a8;
  --line:#3a3b40;
}
*{margin:0;padding:0;box-sizing:border-box}
html,body{width:789px;height:1200px;overflow:hidden}
body{font-family:'Roboto',Arial,sans-serif;background:var(--white);position:relative}
.abs{position:absolute}
.hero{left:0;top:0;width:789px;height:415px;background:linear-gradient(180deg,#6e6e70 0%,#8a8b8c 35%,#6a6b6d 60%,#3c3c3e 100%)}
.hero-band{left:0;top:347px;width:789px;height:68px;background:rgba(25,25,27,.78)}
.nav{left:62px;top:30px;display:flex;gap:22px}
.nav a{color:var(--white);font-size:14px;font-weight:500;text-decoration:none}
.brand{display:flex;align-items:center;gap:6px}
.brand-mark{width:30px;height:30px;background:var(--blue)}
.brand-name{font-weight:700;color:#1e1e20;line-height:1;text-transform:uppercase}
.hero-brand{left:0;width:789px;top:97px;justify-content:center}
.hero-brand .brand-name{font-size:20px;color:#1c1d22}
.hero-title{left:0;width:789px;top:184px;text-align:center;color:var(--white);font-size:23px;font-weight:700}
.hero-sub{left:0;width:789px;top:216px;text-align:center;color:var(--white);font-size:13px;font-weight:300;letter-spacing:.3px;text-transform:uppercase}
.quote-input{left:257px;top:362px;width:183px;height:30px;border:1px solid #555;border-right:none;border-radius:3px 0 0 3px;background:rgba(20,20,22,.6);color:#bbb;font-size:8.5px;padding:10px 14px}
.quote-btn{left:439px;top:362px;width:83px;height:30px;background:var(--blue);color:var(--white);font-size:11px;font-weight:500;text-align:center;line-height:30px;border-radius:0 3px 3px 0}
.intro-title{left:0;width:789px;top:438px;text-align:center;color:var(--blue-text);font-size:20px;font-weight:300}
.intro-text{left:224px;width:341px;top:469px;text-align:center;color:var(--grey-text);font-size:10px;font-weight:300;line-height:14.5px}
.btn-solid{background:var(--blue);color:var(--white);border-radius:2px;font-size:8px;font-weight:500;display:flex;align-items:center;justify-content:center;gap:6px}
.intro-btn{left:342px;top:523px;width:106px;height:22px}
.panel-text{color:var(--white);text-align:center}
.panel-text h2{font-size:13px;font-weight:700;margin-bottom:8px}
.panel-text p{font-size:7.5px;line-height:11px;font-weight:400}
.btn-outline{border:1px solid var(--white);border-radius:3px;color:var(--white);font-size:8px;font-weight:500;width:73px;height:23px;line-height:21px;text-align:center;margin:16px auto 0}
.res-panel{left:0;top:577px;width:436px;height:176px;background:var(--dark)}
.res-text{left:228px;top:617px;width:143px}
.res-photo{left:439px;top:577px;width:350px;height:176px;background:linear-gradient(135deg,#3a1d14 0%,#6b3324 40%,#2a1a1c 70%,#141418 100%)}
.com-photo{left:0;top:755px;width:351px;height:174px;background:linear-gradient(160deg,#9c9a93 0%,#b8a58a 45%,#7d6a50 75%,#3c3934 100%)}
.com-panel{left:353px;top:755px;width:436px;height:174px;background:var(--blue)}
.com-text{left:433px;top:779px;width:141px}
.cta{left:0;top:929px;width:789px;height:64px;background:var(--cta);overflow:hidden}
.cta-text{left:195px;top:947px;color:var(--white);font-size:20px;font-weight:300}
.cta-btn{left:511px;top:944px;width:94px;height:31px;font-size:12px}
.footer{left:0;top:993px;width:789px;height:207px;background:var(--footer)}
.footer-brand{left:97px;top:1021px}
.footer-brand .brand-mark{width:20px;height:20px}
.footer-brand .brand-name{font-size:13px;color:var(--white)}
.footer-about{left:97px;top:1054px;width:270px;color:var(--footer-text);font-size:8.5px;line-height:12.8px}
.copy{left:97px;top:1116px;color:var(--footer-text);font-size:7.5px}
.foot-head{color:var(--white);font-size:9px;font-weight:500}
.contact-head{left:455px;top:1028px}
.contact-lines{left:455px;top:1045px;color:#7d7e82;font-size:8.5px;line-height:14px}
.follow-head{left:605px;top:1028px}
.social{left:605px;top:1047px;display:flex;gap:10px}
.social span{width:8px;height:8px;border-radius:50%;background:#c9cacc;display:block}
.divider{left:97px;top:1153px;width:595px;height:1px;background:var(--line)}
.payments{left:97px;top:1172px;display:flex;gap:14px}
.payments span{height:13px;border-radius:2px;background:#4a4b50;display:block}
.top-label{left:645px;top:1172px;color:#c9cacc;font-size:8px}
.top-btn{left:669px;top:1166px}
</style>
</head>
<body>
  <div class="abs hero" role="img" aria-label="Photo of a modern open-plan kitchen and dining area with pendant lamps"></div>
  <div class="abs hero-band"></div>
  <nav class="abs nav"><a href="#">About</a><a href="#">Services</a><a href="#">Gallery</a><a href="#">Contact</a></nav>
  <div class="abs brand hero-brand"><span class="brand-mark"></span><span class="brand-name">Vantage Interiors</span></div>
  <h1 class="abs hero-title">Stylish, Innovative Workmanship</h1>
  <p class="abs hero-sub">Symbol of extraordinary space and great design</p>
  <div class="abs quote-input">Enter your e-mail here</div>
  <div class="abs quote-btn">Quote Today</div>

  <h2 class="abs intro-title">Through stylish, innovative workmanship</h2>
  <p class="abs intro-text">Vantage Interiors’ exclusive architectural and interior projects offer style and comfort for any space, creating a multi-functional cutting edge look for your interior environment.</p>
  <div class="abs btn-solid intro-btn">
    <svg width="9" height="8" viewBox="0 0 9 8"><g fill="#fff"><rect x="0" y="0" width="2" height="2"/><rect x="3" y="0" width="6" height="2"/><rect x="0" y="3" width="2" height="2"/><rect x="3" y="3" width="6" height="2"/><rect x="0" y="6" width="2" height="2"/><rect x="3" y="6" width="6" height="2"/></g></svg>
    Read all about us
  </div>

  <div class="abs res-panel"></div>
  <div class="abs panel-text res-text">
    <h2>Residential</h2>
    <p>Vantage Interiors has the right look and feel for you. We can make a new kitchen look like it should be lived in or bring an old kitchen back to life.</p>
    <div class="btn-outline">Read more</div>
  </div>
  <div class="abs res-photo" role="img" aria-label="Photo of a lounge chair in a living room with bookshelves"></div>

  <div class="abs com-photo" role="img" aria-label="Photo of a commercial reception area with a timber counter"></div>
  <div class="abs com-panel"></div>
  <div class="abs panel-text com-text">
    <h2>Commercial</h2>
    <p>We can satisfy the needs of any interior project, whether it is a luxurious and glamorous space, something that provides high durability, or a contemporary design, a timeless place is truly an investment of comfort and quality.</p>
    <div class="btn-outline">Read more</div>
  </div>

  <div class="abs cta">
    <svg width="789" height="64" viewBox="0 0 789 64"><polygon points="0,0 430,0 470,64 0,64" fill="#1f2023"/></svg>
  </div>
  <p class="abs cta-text">Take a look at all what we offer you</p>
  <div class="abs btn-solid cta-btn">Check it Out</div>

  <footer class="abs footer"></footer>
  <div class="abs brand footer-brand"><span class="brand-mark"></span><span class="brand-name">Vantage Interiors</span></div>
  <p class="abs footer-about">The Vantage Interiors team have over 20 years experience in the design, building, vinyl application and signage trades, giving us the ability to work through any creative or architectural needs your project may require.</p>
  <p class="abs copy">© 2016 Vantage Interiors All rights reserved</p>
  <p class="abs foot-head contact-head">Contact Us</p>
  <p class="abs contact-lines">info@vantageinteriors.com.au<br>02 9000 4512</p>
  <p class="abs foot-head follow-head">Follow Us</p>
  <div class="abs social"><span></span><span></span><span></span><span></span></div>
  <div class="abs divider"></div>
  <div class="abs payments"><span style="width:26px"></span><span style="width:24px"></span><span style="width:24px"></span><span style="width:48px"></span><span style="width:16px"></span><span style="width:36px"></span></div>
  <p class="abs top-label">Top</p>
  <svg class="abs top-btn" width="24" height="24" viewBox="0 0 24 24"><circle cx="12" cy="12" r="11" fill="none" stroke="#c9cacc" stroke-width="1"/><polyline points="8.5,13.5 12,10 15.5,13.5" fill="none" stroke="#c9cacc" stroke-width="1.4"/></svg>
</body>
</html>
```